Building company buisness cards

We are looking for a sharp modern new look for our business cards.We are a New Zealand based company that specialises in house and land packages.We have attached a photo of the current logo and would like to see if it can be improved somehow if needed.We are open to any colours but we have chosen Black and White at this stage. Feel free to change the font and make the logo smarter looking.Play with the colours and see what looks best.We want a card that looks so good know one will want to throw it away!

Target Market(s)

Building profesonals, home buyers

Industry/Entity Type

Building

Contact Information for Business Card

Garrick Tenwood
0275390628
garrickt@hartvale.co.nz

Font styles to use
Serif
Sans Serif

Colors

Designer to choose colors to be used in the design.

Requirements
Must have
• Just the logo on one side and details on the other
• Clean simple looking card
Nice to have
• Round corners and detail like raised or spot UV
• Something that stands out
Should not have
• To title needed, Director etc

```html
<!DOCTYPE html>
<html lang="en">
<head>
<meta charset="utf-8">
<title>Hartvale Business Card</title>
<link rel="stylesheet" href="https://fonts.googleapis.com/css2?family=Jost:wght@400;500;600&display=swap">
<style>
  :root {
    --navy: #1d2858;
    --paper: #ffffff;
    --backdrop: #d9d9d9;
    --ink-light: #ffffff;
  }
  * { margin: 0; padding: 0; box-sizing: border-box; }
  html, body {
    width: 1125px;
    height: 1200px;
    overflow: hidden;
    background: var(--backdrop);
    font-family: "Jost", "Futura", sans-serif;
  }
  .sheet {
    position: relative;
    width: 1125px;
    height: 1200px;
  }
  .card {
    position: absolute;
    left: 156px;
    width: 825px;
    height: 471px;
    border-radius: 26px;
  }
  .card--back {
    top: 106px;
    background: var(--navy);
    color: var(--ink-light);
  }
  .card--front {
    top: 639px;
    background: var(--paper);
  }
  .details {
    position: absolute;
    left: 50%;
    top: 167px;
    transform: translateX(-50%);
    width: 224px;
    text-align: center;
  }
  .details__name {
    font-size: 29px;
    font-weight: 400;
    line-height: 1;
    padding-bottom: 14px;
    white-space: nowrap;
  }
  .details__rule {
    height: 1px;
    background: rgba(255, 255, 255, 0.85);
  }
  .details__email {
    font-size: 17px;
    letter-spacing: 0;
    line-height: 1;
    padding: 19px 0 20px;
    white-space: nowrap;
  }
  .details__phone {
    font-size: 19.5px;
    letter-spacing: 0.6px;
    line-height: 1;
    padding-top: 22px;
  }
  .brand {
    position: absolute;
    left: 50%;
    top: 50%;
    transform: translate(-50%, -50%);
  }
  .brand__name {
    display: block;
    font-size: 128px;
    font-weight: 600;
    color: var(--navy);
    line-height: 1;
    letter-spacing: -1px;
    white-space: nowrap;
  }
</style>
</head>
<body>
  <main class="sheet">
    <section class="card card--back" aria-label="Contact side">
      <div class="details">
        <p class="details__name">Garrick Tenwood</p>
        <div class="details__rule"></div>
        <p class="details__email">GARRICKT@HARTVALE.CO.NZ</p>
        <div class="details__rule"></div>
        <p class="details__phone">P. 0275390628</p>
      </div>
    </section>
    <section class="card card--front" aria-label="Brand side">
      <div class="brand">
        <span class="brand__name">Hartvale</span>
      </div>
    </section>
  </main>
</body>
</html>
```